Maple9Tone

I need a website designed to feature a new product for my company. I am dedicating a separate site just highlight the program. The url will be maple9tone.com and the product name is maple tone. The product is ringless voicemail. We take a recorded script and send it to our clients customers cell phones without the phone ringing.

The site will consist of a home page. I animated video demo. It will house 18 scripts and voice overs to match, a results page, and a page to request a live demo.

We sell the product to new car dealerships

```html
<!DOCTYPE html>
<html lang="en">
<head>
<meta charset="utf-8">
<title>Maple9Tone – Ringless Voicemail for Dealerships</title>
<link href="https://fonts.googleapis.com/css2?family=Roboto:wght@400;500;700&display=swap" rel="stylesheet">
<style>
:root{
  --navy:#0a5a86;
  --blue:#0e6596;
  --link:#0d5e8d;
  --teal:#4aa9bf;
  --ink:#222;
  --body:#555;
  --line:#d6d6d6;
  --paper:#fff;
  --footer:#ececec;
  --base:#3a3a3a;
  --dark:#2a2d31;
}
*{box-sizing:border-box;margin:0;padding:0}
html,body{width:1200px;height:3066px;overflow:hidden}
body{font-family:"Roboto",Arial,sans-serif;color:var(--ink);background:var(--paper);position:relative}
section,header,nav,footer{position:absolute;left:0;width:1200px}
.abs{position:absolute}

/* header */
.site-header{top:0;height:102px;background:var(--paper)}
.brand{left:86px;top:30px;display:flex;align-items:center;gap:12px;font-weight:700;font-size:22px;color:var(--ink)}
.brand-dot{width:40px;height:40px;border-radius:50%;background:var(--navy)}
.header-btn{top:25px;height:51px;border:2px solid var(--navy);display:flex;align-items:center;justify-content:center;gap:12px;font-size:21px;color:var(--ink)}
.header-btn svg{width:26px;height:26px;fill:var(--navy)}
.btn-phone{left:746px;width:205px}
.btn-signin{left:971px;width:141px}

/* nav */
.main-nav{top:102px;height:49px;background:var(--navy)}
.nav-item{top:0;line-height:49px;color:#fff;font-size:12px;font-weight:500;text-transform:uppercase}
.nav-item.has-menu::after{content:"";display:inline-block;margin-left:10px;width:5px;height:5px;border-right:1.5px solid #fff;border-bottom:1.5px solid #fff;transform:rotate(45deg) translateY(-3px)}
.nav-search{left:953px;top:8px;width:159px;height:34px;border:1px solid #fff;color:#cfe2ee;font-size:12px;padding:9px 10px}
.nav-search svg{position:absolute;right:9px;top:8px;width:17px;height:17px}

/* hero */
.hero{top:151px;height:432px;background:var(--teal)}
.hero-art{left:40px;top:20px;width:540px;height:412px;background:linear-gradient(160deg,#5fb8cc 0%,#3f9cb3 100%);border-radius:4px}
.hero-title{right:88px;top:136px;font-size:46px;font-weight:700;color:#fff;letter-spacing:.5px}
.hero-sub{right:88px;top:196px;font-size:21px;color:#fff}
.play-btn{left:950px;top:241px;width:160px;height:49px;border:2px solid #fff;color:#fff;font-size:14px;font-weight:700;display:flex;align-items:center;justify-content:center;gap:10px}
.slide-arrow{width:32px;height:32px;border-radius:50%;background:rgba(255,255,255,.55);top:203px}
.slide-arrow svg{width:32px;height:32px}

/* about */
.about{top:583px;height:368px;text-align:center}
.section-title{font-size:25px;font-weight:500;color:var(--ink);text-align:center;text-transform:uppercase}
.section-title::after{content:"";display:block;width:44px;height:3px;background:var(--navy);margin:14px auto 0}
.about .section-title{position:absolute;top:62px;width:100%}
.about-text{left:210px;top:131px;width:780px;font-size:14px;line-height:21px;color:var(--body);text-align:justify;text-align-last:center}
.outline-btn{left:541px;top:255px;width:118px;height:42px;border:2px solid var(--navy);line-height:38px;font-size:14px;font-weight:500;color:var(--ink)}

/* how it works */
.how{top:951px;height:674px;background:var(--blue)}
.how-frame{left:14px;top:14px;width:1172px;height:646px;border:1px solid rgba(255,255,255,.7)}
.how .section-title{position:absolute;top:68px;width:100%;color:#fff}
.how .section-title::after{display:none}
.how-map{left:0;top:0}
.step-text{width:200px;color:#fff;font-size:13px;line-height:16px;text-align:center}

/* cards */
.cards{top:1625px;height:464px;background:var(--paper)}
.card{background:#fff;box-shadow:0 2px 8px rgba(0,0,0,.22)}
.card-sample{left:86px;top:72px;width:621px;height:306px}
.sample-art{left:14px;top:14px;width:248px;height:280px;background:linear-gradient(90deg,#3b9aa3 0 50%,#d9962f 50% 100%)}
.sample-body{left:290px;top:45px;width:310px}
.card-title{font-size:19px;font-weight:500;color:var(--link);text-transform:uppercase;margin-bottom:10px}
.sample-body p{font-size:13px;line-height:22px;color:var(--body);text-align:justify}
.read-more{display:block;margin-top:10px;font-size:14px;font-weight:500;color:var(--link)}
.card-offer{left:742px;top:72px;width:372px;height:306px}
.offer-box{left:16px;top:12px;width:340px;height:282px;border:2px solid var(--link);padding:32px 14px 0 14px}
.offer-list{list-style:none;margin-top:6px}
.offer-list li{display:flex;gap:12px;font-size:12.5px;line-height:18px;color:var(--body);margin-bottom:13px}
.tick{flex:0 0 16px;height:16px;background:var(--link);margin-top:1px}
.tick svg{width:16px;height:16px}

/* scripts */
.scripts{top:2089px;height:358px;background:linear-gradient(180deg,#2b2f33 0%,#1f2225 60%,#34383c 100%)}
.scripts .section-title{position:absolute;top:72px;width:100%;color:#fff}
.scripts .section-title::after{display:none}
.month{width:76px;height:76px;border-radius:50%;border:3px solid #1b6e9e;background:#1a1d20;color:#fff;font-size:13px;font-weight:500;display:flex;align-items:center;justify-content:center;top:162px}
.script-name{top:260px;width:220px;text-align:center;color:#fff;font-size:15px;font-weight:700;text-transform:uppercase}
.carousel-arrow{top:210px;width:20px;height:22px}

/* partners */
.partners{top:2447px;height:329px}
.partners .section-title{position:absolute;top:58px;width:100%}
.partners .section-title::after{display:none}
.partner{top:155px;width:199px;height:102px;border:1px solid var(--line);display:flex;align-items:center;justify-content:center}
.partner-badge{width:120px;height:30px;background:#c9ccd0;border-radius:3px}

/* footer */
.site-footer{top:2776px;height:241px;background:var(--footer)}
.footer-heading{top:42px;font-size:17px;font-weight:500;color:var(--ink);text-transform:uppercase}
.footer-list{list-style:none;font-size:12.5px;color:#444}
.contact-list li{display:flex;gap:14px;margin-bottom:18px;line-height:16px}
.contact-list svg{flex:0 0 16px;width:16px;height:16px;fill:var(--navy)}
.link-list li{margin-bottom:14px;line-height:17px}
.link-list li::before{content:"»";color:var(--navy);margin-right:12px;font-weight:700}
.follow-list li{display:flex;gap:12px;align-items:center;margin-bottom:13px;line-height:17px}
.follow-list span.box{width:13px;height:13px;background:var(--navy)}
.news-input{left:844px;top:88px;width:270px;height:37px;border-radius:19px;background:#e2e2e2;border:1px solid #d4d4d4;font-size:11px;color:#999;padding:11px 16px}
.news-btn{left:844px;top:141px;width:96px;height:37px;border-radius:19px;background:var(--navy);color:#fff;font-size:12px;font-weight:500;line-height:37px;text-align:center;text-transform:uppercase}
.base-bar{top:3017px;height:49px;background:var(--base);color:#fff;font-size:12.5px;text-align:center;line-height:49px}
</style>
</head>
<body>

<header class="site-header">
  <div class="brand abs"><span class="brand-dot"></span>MAPLE9TONE</div>
  <div class="header-btn btn-phone abs">
    <svg viewBox="0 0 24 24"><path d="M6.6 10.8a15.1 15.1 0 0 0 6.6 6.6l2.2-2.2c.3-.3.7-.4 1-.2 1.1.4 2.3.6 3.6.6.6 0 1 .4 1 1V20c0 .6-.4 1-1 1A17 17 0 0 1 3 4c0-.6.4-1 1-1h3.5c.6 0 1 .4 1 1 0 1.3.2 2.5.6 3.6.1.3 0 .7-.2 1z"/></svg>
    303 555 0142
  </div>
  <div class="header-btn btn-signin abs">
    <svg viewBox="0 0 24 24"><circle cx="12" cy="8" r="4.5"/><path d="M3 21c0-5 4-8 9-8s9 3 9 8z"/></svg>
    SIGN IN
  </div>
</header>

<nav class="main-nav">
  <span class="nav-item abs" style="left:86px">Home</span>
  <span class="nav-item abs" style="left:178px">About Us</span>
  <span class="nav-item has-menu abs" style="left:294px">How It Works</span>
  <span class="nav-item has-menu abs" style="left:462px">The Offer</span>
  <span class="nav-item has-menu abs" style="left:605px">Available Scripts</span>
  <span class="nav-item abs" style="left:803px">Contact Us</span>
  <div class="nav-search abs">Search..
    <svg viewBox="0 0 24 24" fill="none" stroke="#fff" stroke-width="3"><circle cx="10" cy="10" r="7"/><path d="M15 15l7 7"/></svg>
  </div>
</nav>

<section class="hero">
  <div class="hero-art abs" role="img" aria-label="Illustration of a call-centre agent at a desk speaking with a customer on the phone"></div>
  <h1 class="hero-title abs">MAPLE TONE</h1>
  <p class="hero-sub abs">Fast, Effective, Inexpensive, Versatile Marketing</p>
  <div class="play-btn abs">
    <svg width="24" height="24" viewBox="0 0 24 24" fill="none" stroke="#fff" stroke-width="2"><circle cx="12" cy="12" r="10"/><path d="M10 8l6 4-6 4z" fill="#fff"/></svg>
    PLAY VIDEO
  </div>
  <div class="slide-arrow abs" style="left:21px"><svg viewBox="0 0 32 32"><path d="M19 9l-7 7 7 7" fill="none" stroke="#fff" stroke-width="3"/></svg></div>
  <div class="slide-arrow abs" style="left:1143px"><svg viewBox="0 0 32 32"><path d="M13 9l7 7-7 7" fill="none" stroke="#fff" stroke-width="3"/></svg></div>
</section>

<section class="about">
  <h2 class="section-title">About Us</h2>
  <p class="about-text abs">We select a targeted list of past sales customers, service customers, or unsold leads.We develop and record a script based on your stores current needs, incentives, time of year, and list.Your team will be coached and given a set of scripted responses to be sure everyone is prepared.Your message and list are uploaded to our system and delivered at any speed you wish.Inbound return calls will begin within minutes.This program requires zero set up.The simple process above can be completed and go live in as little as 24 hours.</p>
  <div class="outline-btn abs">READ MORE</div>
</section>

<section class="how">
  <div class="how-frame abs"></div>
  <h2 class="section-title">How It Works</h2>
  <svg class="how-map abs" width="1200" height="674" viewBox="0 0 1200 674">
    <defs>
      <marker id="arrowhead" markerWidth="8" markerHeight="8" refX="7" refY="4" orient="auto"><path d="M0 0L8 4L0 8z" fill="#fff"/></marker>
      <polygon id="hex" points="0,-45 39,-22.5 39,22.5 0,45 -39,22.5 -39,-22.5" fill="none" stroke="#fff" stroke-width="2"/>
    </defs>
    <g stroke="#fff" stroke-width="1" stroke-dasharray="3 3" fill="none">
      <path d="M255 200H415" marker-end="url(#arrowhead)"/>
      <path d="M504 200H662" marker-end="url(#arrowhead)"/>
      <path d="M751 200H912" marker-end="url(#arrowhead)"/>
      <path d="M1001 200H1079V378H213V432" marker-end="url(#arrowhead)"/>
      <path d="M255 484H415" marker-end="url(#arrowhead)"/>
      <path d="M504 484H662" marker-end="url(#arrowhead)"/>
      <path d="M751 484H912" marker-end="url(#arrowhead)"/>
    </g>
    <g fill="#fff" font-family="Roboto, Arial, sans-serif" font-size="32" font-weight="500" text-anchor="middle">
      <use href="#hex" x="213" y="200"/><text x="213" y="211">1</text>
      <use href="#hex" x="462" y="200"/><text x="462" y="211">2</text>
      <use href="#hex" x="709" y="200"/><text x="709" y="211">3</text>
      <use href="#hex" x="959" y="200"/><text x="959" y="211">4</text>
      <use href="#hex" x="213" y="484"/><text x="213" y="495">5</text>
      <use href="#hex" x="462" y="484"/><text x="462" y="495">6</text>
      <use href="#hex" x="709" y="484"/><text x="709" y="495">7</text>
      <use href="#hex" x="959" y="484"/><text x="959" y="495">8</text>
    </g>
  </svg>
  <p class="step-text abs" style="left:113px;top:264px">We select a targeted list of past sales customers, service customers, or unsold leads.</p>
  <p class="step-text abs" style="left:362px;top:264px">We develop and record a script based on your stores current needs, incentives, time of year, and list.</p>
  <p class="step-text abs" style="left:609px;top:264px">Your team will be coached and given a set of scripted responses to be sure everyone is prepared.</p>
  <p class="step-text abs" style="left:859px;top:264px">Your message and list are uploaded to our system and delivered at any speed you wish.</p>
  <p class="step-text abs" style="left:113px;top:548px">Inbound return calls will begin within minutes.</p>
  <p class="step-text abs" style="left:362px;top:548px">This program requires zero set up.</p>
  <p class="step-text abs" style="left:609px;top:548px">The simple process above can be completed and go live in as little as 24 hours.</p>
  <p class="step-text abs" style="left:859px;top:548px">Every inbound phone call is recorded, tracked, and caller id information is captured.</p>
</section>

<section class="cards">
  <article class="card card-sample abs">
    <div class="sample-art abs" role="img" aria-label="Illustration of an office with two agents working at desks on the phone"></div>
    <div class="sample-body abs">
      <h3 class="card-title">Sample Script</h3>
      <p>Hi this is (Managers Name), I'm the (Title) at (Dealership). I have a customer that's interested in a car like the one you purchased from us and I'm hoping you would be interested in allowing us to buy it back from you?I'd be willing to pay you up to 125% oAgain, this is (Managers First Name) at (Dealership) - my number is (our tracking number to be added). Talk to you soon. Bye</p>
      <span class="read-more">READ MORE &gt;&gt;</span>
    </div>
  </article>
  <article class="card card-offer abs">
    <div class="offer-box abs">
      <h3 class="card-title">The Offer</h3>
      <ul class="offer-list">
        <li><span class="tick"><svg viewBox="0 0 16 16"><path d="M4 8l3 3 5-6" fill="none" stroke="#fff" stroke-width="2"/></svg></span>We can use this as a buy back offer, re-engage unsold CRM leads, offer monthly factory incentives, inform of a sales event, or to get CSI surveys completed</li>
        <li><span class="tick"><svg viewBox="0 0 16 16"><path d="M4 8l3 3 5-6" fill="none" stroke="#fff" stroke-width="2"/></svg></span>Can be recorded by anyone!</li>
        <li><span class="tick"><svg viewBox="0 0 16 16"><path d="M4 8l3 3 5-6" fill="none" stroke="#fff" stroke-width="2"/></svg></span>Works because the message is perfect every time!</li>
        <li><span class="tick"><svg viewBox="0 0 16 16"><path d="M4 8l3 3 5-6" fill="none" stroke="#fff" stroke-width="2"/></svg></span>The information stays with them!</li>
      </ul>
    </div>
  </article>
</section>

<section class="scripts" role="img" aria-label="Dimmed photo of an empty office with desks and chairs">
  <h2 class="section-title">Available Scripts</h2>
  <svg class="carousel-arrow abs" style="left:80px" viewBox="0 0 20 22"><path d="M13 4l-7 7 7 7" fill="none" stroke="#fff" stroke-width="3"/></svg>
  <svg class="carousel-arrow abs" style="left:1097px" viewBox="0 0 20 22"><path d="M7 4l7 7-7 7" fill="none" stroke="#fff" stroke-width="3"/></svg>
  <div class="month abs" style="left:175px">January</div>
  <div class="month abs" style="left:430px">February</div>
  <div class="month abs" style="left:698px">March</div>
  <div class="month abs" style="left:953px">April</div>
  <p class="script-name abs" style="left:103px">New Years</p>
  <p class="script-name abs" style="left:358px">Winter Special</p>
  <p class="script-name abs" style="left:626px">Spring Forward</p>
  <p class="script-name abs" style="left:881px">Tax Time</p>
</section>

<section class="partners">
  <h2 class="section-title">Our Partners</h2>
  <div class="partner abs" style="left:164px"><span class="partner-badge"></span></div>
  <div class="partner abs" style="left:388px"><span class="partner-badge"></span></div>
  <div class="partner abs" style="left:613px"><span class="partner-badge"></span></div>
  <div class="partner abs" style="left:838px"><span class="partner-badge"></span></div>
</section>

<footer class="site-footer">
  <h4 class="footer-heading abs" style="left:86px">Contact Us</h4>
  <ul class="footer-list contact-list abs" style="left:86px;top:84px;width:200px">
    <li><svg viewBox="0 0 24 24"><path d="M12 2a7 7 0 0 0-7 7c0 5 7 13 7 13s7-8 7-13a7 7 0 0 0-7-7zm0 9.5a2.5 2.5 0 1 1 0-5 2.5 2.5 0 0 1 0 5z"/></svg><span>27B Cedar Lane<br>Suite 12</span></li>
    <li><svg viewBox="0 0 24 24"><path d="M6.6 10.8a15.1 15.1 0 0 0 6.6 6.6l2.2-2.2c.3-.3.7-.4 1-.2 1.1.4 2.3.6 3.6.6.6 0 1 .4 1 1V20c0 .6-.4 1-1 1A17 17 0 0 1 3 4c0-.6.4-1 1-1h3.5c.6 0 1 .4 1 1 0 1.3.2 2.5.6 3.6.1.3 0 .7-.2 1z"/></svg><span>303 555 0142</span></li>
    <li><svg viewBox="0 0 24 24"><path d="M2 5h20v14H2z"/><path d="M2 5l10 8 10-8" fill="none" stroke="#ececec" stroke-width="2"/></svg><span>info@maple9tone.com</span></li>
  </ul>

  <h4 class="footer-heading abs" style="left:313px">Quick Links</h4>
  <ul class="footer-list link-list abs" style="left:313px;top:86px">
    <li>Home</li><li>About us</li><li>How It Works</li><li>The Offer</li>
  </ul>
  <ul class="footer-list link-list abs" style="left:443px;top:80px">
    <li>The Offer</li><li>Contact us</li><li>FAQ</li><li>Terms and conditions</li>
  </ul>

  <h4 class="footer-heading abs" style="left:660px">Follow Us</h4>
  <ul class="footer-list follow-list abs" style="left:660px;top:84px">
    <li><span class="box"></span>Linkvine</li>
    <li><span class="box"></span>Chirpline</li>
    <li><span class="box"></span>Snapgrid</li>
    <li><span class="box"></span>Streamly</li>
  </ul>

  <h4 class="footer-heading abs" style="left:844px">Newsletter</h4>
  <div class="news-input abs">E-mail address...</div>
  <div class="news-btn abs">Subscribe</div>
</footer>

<div class="base-bar abs" style="left:0;width:1200px">@copyright 2016 Maple9Tone.All Rights Reserved</div>

</body>
</html>
```